****Business Card Design for Quarrystone Development. Design based around attached logo/company name

I’m looking for business card design for my company Quarrystone Development Group,LLC. Design should be professional, sharp and minimal. Outside of the attached logos, greyscale colors for remainder of cards. My thoughts are two-sided card with attached logo on one side and my info on the other but open to one-sided as well with right design.
Target Market(s)
Real estate professionals including banks, private investors, property owners, developers, commercial tenants like Brewlantern, Grovika or Tanquist’s.
Industry/Entity Type
Commercial real estate development and investments.
Contact Information for Business Card
Name, title, email, phone #’s, web address and physical address
Font styles to use
Other font styles liked:
- Helvetica, Garamond, etc
Colors
Designer to choose only greyscale colors for use in the design.
Requirements
Must have
- Attached logo first or second options.
Nice to have
- Two sided card with logo on one side. Attached Logo/company name can be laid out any way that flows as long as it’s legible.name
Should not have
- No loud colors. ***Please do not include logo, I have removed the company design with a logo image.

```html
<!DOCTYPE html>
<html lang="en">
<head>
<meta charset="utf-8">
<title>Quarrystone Development Group, LLC — Business Card</title>
<link href="https://fonts.googleapis.com/css2?family=Libre+Baskerville:wght@400;700&family=Arimo:wght@400&display=swap" rel="stylesheet">
<style>
  :root {
    --backdrop: #2b2b2d;
    --card: #ffffff;
    --slate: #5b6577;
    --ink-name: #5a6475;
    --ink-body: #8a8a8c;
    --on-slate: #ffffff;
  }
  html, body {
    margin: 0;
    width: 1200px;
    height: 901px;
    overflow: hidden;
    background: var(--backdrop);
  }
  .card {
    position: absolute;
    left: 110px;
    top: 165px;
    width: 980px;
    height: 560px;
    background: var(--card);
    box-shadow: 0 10px 30px rgba(0,0,0,0.45);
  }
  .brand-panel {
    position: absolute;
    left: 70px;
    top: 70px;
    width: 450px;
    height: 420px;
    background: var(--slate);
    border-radius: 30px;
    display: flex;
    flex-direction: column;
    justify-content: center;
    align-items: center;
    text-align: center;
  }
  .brand-name {
    margin: 0;
    font-family: "Libre Baskerville", serif;
    font-weight: 400;
    color: var(--on-slate);
    font-size: 30px;
    line-height: 1.35;
    letter-spacing: 1.5px;
    text-transform: uppercase;
  }
  .contact {
    position: absolute;
    left: 575px;
    top: 165px;
    font-family: "Arimo", sans-serif;
    color: var(--ink-body);
  }
  .person-name {
    margin: 0;
    font-family: "Libre Baskerville", serif;
    font-weight: 700;
    color: var(--ink-name);
    font-size: 26px;
    letter-spacing: 0.5px;
    text-transform: uppercase;
  }
  .person-title {
    margin: 2px 0 22px;
    font-size: 21px;
  }
  .address {
    font-style: normal;
    font-size: 21px;
    line-height: 1.3;
    margin-bottom: 22px;
  }
  .contact-list {
    list-style: none;
    margin: 0;
    padding: 0;
    font-size: 21px;
  }
  .contact-list li {
    display: flex;
    align-items: center;
    gap: 12px;
    height: 34px;
  }
  .contact-list .icon {
    width: 16px;
    height: 16px;
    flex: none;
    fill: var(--ink-name);
  }
  .contact-list .no-icon { padding-left: 28px; }
</style>
</head>
<body>
  <div class="card">
    <div class="brand-panel">
      <p class="brand-name">Quarrystone<br>Development<br>Group, LLC</p>
    </div>

    <div class="contact">
      <h1 class="person-name">Dorian Vaskell</h1>
      <p class="person-title">Founder/CEO</p>
      <address class="address">2190 Ledgeview Parkway<br>Harlow Springs AB 3062</address>
      <ul class="contact-list">
        <li>
          <svg class="icon" viewBox="0 0 16 16" aria-hidden="true"><path d="M3.2 1.5l2.3 2.6-1.2 1.8c.9 2 2.4 3.6 4.4 4.6l1.8-1.2 2.6 2.3-1.3 2.2C6.8 13.4 2.6 9.2 1.2 3.3z"/></svg>
          <span>(555)-310-4827</span>
        </li>
        <li>
          <svg class="icon" viewBox="0 0 16 16" aria-hidden="true"><path d="M1 3h14v1.2L8 9 1 4.2z M1 5.6l7 4.8 7-4.8V13H1z"/></svg>
          <span>info@quarrystonedevelopment.com</span>
        </li>
        <li>
          <svg class="icon" viewBox="0 0 16 16" aria-hidden="true"><circle cx="8" cy="8" r="7"/></svg>
          <span>www.quarrystonedevelopment.com</span>
        </li>
        <li class="no-icon"><span>www.quarrystonedevelopment.com</span></li>
      </ul>
    </div>
  </div>
</body>
</html>
```